Commercial Real Estate

We need a business card design for a new commercial real estate business that specializes in apartment building brokerage. Not individual units but the entire complex. We find and represent the owners existing buildings and well as new buyers for those buildings. The design should convey trust, integrity, knowledge and growth. It should be easily read.

Target Market(s)

40 to 65 years old

Industry/Entity Type

Real Estate

```html
<!DOCTYPE html>
<html lang="en">
<head>
<meta charset="utf-8">
<title>Halvern Property Investments – Business Card</title>
<link rel="stylesheet" href="https://fonts.googleapis.com/css2?family=Roboto:wght@300;400;700&display=swap">
<style>
  :root {
    --backdrop: #d9d9d7;
    --card: #f0f0ef;
    --ink: #4a4f50;
    --ink-soft: #6a6f70;
    --teal: #5bb0ae;
    --slate: #3d4748;
  }
  * { box-sizing: border-box; margin: 0; padding: 0; }
  html, body {
    width: 1200px;
    height: 900px;
    overflow: hidden;
    background: var(--backdrop);
    font-family: "Roboto", Arial, sans-serif;
    color: var(--ink);
  }
  .sheet {
    width: 1200px;
    height: 900px;
    display: flex;
    flex-direction: column;
    align-items: center;
    justify-content: center;
    gap: 48px;
  }
  .card {
    width: 660px;
    height: 377px;
    background: var(--card);
    box-shadow: 0 2px 6px rgba(0,0,0,0.12);
    position: relative;
  }
  .brand {
    display: flex;
    align-items: center;
    gap: 14px;
  }
  .brand-mark {
    width: 22px;
    height: 22px;
    background: var(--teal);
  }
  .brand-name {
    font-weight: 700;
    font-size: 40px;
    letter-spacing: 3px;
    color: var(--slate);
    text-transform: uppercase;
  }
  /* Front */
  .card-front {
    display: flex;
    align-items: center;
    justify-content: center;
  }
  /* Back */
  .card-back .brand {
    position: absolute;
    left: 48px;
    bottom: 70px;
  }
  .card-back .brand-name { font-size: 32px; }
  .contact {
    position: absolute;
    left: 350px;
    top: 52px;
    width: 280px;
  }
  .person-name {
    font-weight: 300;
    font-size: 26px;
    color: var(--ink);
  }
  .person-role {
    font-weight: 300;
    font-size: 15px;
    color: var(--ink-soft);
    margin-top: 2px;
  }
  .contact-lines {
    list-style: none;
    margin-top: 18px;
    font-weight: 300;
    font-size: 15px;
    line-height: 1.45;
  }
  .contact-lines .label {
    display: inline-block;
    width: 16px;
    font-weight: 700;
    color: var(--teal);
  }
  .address {
    margin-top: 22px;
    font-weight: 300;
    font-size: 16px;
  }
  .divider {
    margin-top: 30px;
    width: 240px;
    height: 2px;
    background: var(--teal);
  }
  .website {
    margin-top: 20px;
    font-weight: 700;
    font-size: 16px;
    color: var(--slate);
  }
</style>
</head>
<body>
<main class="sheet">
  <section class="card card-front" aria-label="Business card front">
    <div class="brand">
      <span class="brand-mark"></span>
      <span class="brand-name">Halvern</span>
    </div>
  </section>

  <section class="card card-back" aria-label="Business card back">
    <div class="brand">
      <span class="brand-mark"></span>
      <span class="brand-name">Halvern</span>
    </div>
    <div class="contact">
      <p class="person-name">Daniel Mercer</p>
      <p class="person-role">Manager</p>
      <ul class="contact-lines">
        <li><span class="label">T</span>0400 318 542</li>
        <li><span class="label">F</span>0400 318 120</li>
        <li><span class="label">E</span>daniel.mercer@halvern.com</li>
      </ul>
      <p class="address">PO Box 2040 Riverton NT 0830</p>
      <div class="divider"></div>
      <p class="website">www.halvern.com</p>
    </div>
  </section>
</main>
</body>
</html>
```